Refresh Application User Interface

Brightmoor wishes to update the look of its business applications. Two representative forms are shown below. Please note, we are not considering changes in functionality or usability. Our goal is a cleaner, more contemporary design.

Industry/Entity Type

Business

```html
<!DOCTYPE html>
<html lang="en">
<head>
<meta charset="utf-8">
<title>Brightmoor · Purchase Order</title>
<link href="https://fonts.googleapis.com/css2?family=Open+Sans:wght@400;600;700;800&display=swap" rel="stylesheet">
<style>
:root{
  --topbar:#2d3037;
  --topbar-text:#ffffff;
  --logout:#e8485a;
  --ink:#2b2b2b;
  --muted:#8592b0;
  --accent:#2a7fd4;
  --brand:#1f3f93;
  --panel:#f1f2f6;
  --sidebar:#ececf1;
  --line:#dcdfe6;
  --field-border:#d4d7de;
  --green:#5cbf3c;
  --red:#e23a48;
}
*{box-sizing:border-box;margin:0;padding:0}
html,body{width:1200px;height:861px;overflow:hidden;background:#fff;font-family:"Open Sans",sans-serif;color:var(--ink)}
.app{position:relative;width:1200px;height:861px}
.abs{position:absolute;white-space:nowrap}
.topbar{left:0;top:0;width:1200px;height:54px;background:var(--topbar);color:var(--topbar-text);font-size:17px}
.topbar .left{position:absolute;left:15px;top:0;height:54px;display:flex;align-items:center;gap:22px}
.topbar .left > span{display:flex;align-items:center;gap:6px}
.topbar b{font-weight:700}
.topbar .actions{position:absolute;right:20px;top:0;height:54px;display:flex;align-items:center;gap:22px}
.topbar .act{display:flex;align-items:center;gap:8px}
.topbar .logout{color:var(--logout)}
.mainnav span{position:absolute;top:77px;font-size:22px;color:#444}
.mainnav .sep{color:#888}
.mainnav .active{color:var(--accent);font-weight:600}
.brand{left:1008px;top:76px;font-size:25px;font-weight:800;color:var(--brand)}
.subnav span{position:absolute;top:134px;font-size:19px;color:var(--muted)}
.subnav .active{color:var(--ink)}
.subnav-bar{left:27px;top:174px;width:63px;height:4px;background:var(--accent)}
.rule{left:0;top:179px;width:1200px;height:1px;background:var(--line)}
.title{left:26px;top:197px;font-size:24px;font-weight:400}
.lbl{font-size:15px;color:#444}
.val{font-size:13px}
.field{border:1px solid var(--field-border);background:#fff;height:27px;font-size:12px;padding:5px 10px;color:#333}
.field.focus{border-color:var(--accent)}
.link{font-size:15px;color:var(--accent)}
.sidebar{left:1048px;top:180px;width:152px;height:614px}
.sidebar .gray{position:absolute;left:0;top:160px;width:152px;height:454px;background:var(--sidebar)}
.side-item{position:absolute;right:20px;font-size:22px;color:var(--muted);display:flex;align-items:center;gap:10px}
.side-item.done{color:var(--green)}
.panel{left:0;top:512px;width:1048px;height:282px;background:var(--panel)}
.tabs{left:27px;top:527px;font-size:16px;color:var(--muted);display:flex;gap:29px}
.tabs .active{color:var(--ink);position:relative}
.tabs .active:after{content:"";position:absolute;left:0;right:0;bottom:-5px;height:2px;background:var(--ink)}
.row-lbl{font-size:14px;color:#444;text-align:right}
.select{border:1px solid #e1e3e8;background:#fff;height:25px;font-size:12px;padding:4px 9px;color:#333}
.select.drop:after{content:"";position:absolute;right:0;top:0;width:16px;height:23px;background:#eef0f3;border-left:1px solid #e1e3e8}
.select i{position:absolute;right:4px;top:10px;border:4px solid transparent;border-top:5px solid #666;z-index:1}
.toolbar{left:0;top:794px;width:1200px;height:67px;border-top:1px solid var(--line);background:#fff}
.status{left:459px;top:816px;font-size:20px;color:var(--muted)}
.ico{position:absolute}
</style>
</head>
<body>
<div class="app">

  <header class="abs topbar">
    <div class="left">
      <span>Logged In As <b>Dana Whitlow</b> <svg width="15" height="15" viewBox="0 0 16 16"><circle cx="8" cy="8" r="5.5" fill="none" stroke="#fff" stroke-width="3" stroke-dasharray="3 1.5"/><circle cx="8" cy="8" r="2" fill="#fff"/></svg></span>
      <span>Current Role <b>administrator</b> <svg width="14" height="14" viewBox="0 0 14 14"><circle cx="7" cy="7" r="7" fill="#fff"/><path d="M4 6l3 3 3-3z" fill="#2d3037"/></svg></span>
    </div>
    <div class="actions">
      <div class="act"><svg width="26" height="30" viewBox="0 0 26 30"><path d="M9 16V4a2 2 0 014 0v9l7 2c2 .6 3 2 2.5 4l-2 7H10l-5-7c-1-1.5 1-3 2.5-2L9 18" fill="none" stroke="#fff" stroke-width="1.6"/></svg>Touch</div>
      <div class="act"><svg width="30" height="26" viewBox="0 0 30 26"><rect x="1" y="3" width="22" height="16" fill="none" stroke="#fff" stroke-width="1.6"/><rect x="4" y="6" width="22" height="16" fill="none" stroke="#fff" stroke-width="1.6"/><circle cx="24" cy="21" r="5" fill="#5cbf3c"/><path d="M24 18v6M21 21h6" stroke="#fff" stroke-width="1.5"/></svg>New Tab</div>
      <div class="act"><svg width="28" height="28" viewBox="0 0 28 28"><circle cx="14" cy="14" r="12.5" fill="none" stroke="#fff" stroke-width="1.6"/><path d="M10 11a4 4 0 118 0c0 3-4 3-4 6" fill="none" stroke="#fff" stroke-width="1.6"/><circle cx="14" cy="21" r="1.2" fill="#fff"/></svg>Help</div>
      <div class="act"><svg width="28" height="28" viewBox="0 0 28 28"><path d="M5 16v-3a9 9 0 0118 0v3" fill="none" stroke="#fff" stroke-width="1.6"/><rect x="3" y="14" width="4" height="7" rx="1" fill="none" stroke="#fff" stroke-width="1.6"/><rect x="21" y="14" width="4" height="7" rx="1" fill="none" stroke="#fff" stroke-width="1.6"/><path d="M23 21c0 3-4 4-8 4" fill="none" stroke="#fff" stroke-width="1.6"/></svg>Support</div>
      <div class="act logout"><svg width="28" height="30" viewBox="0 0 28 30"><path d="M16 4H3v22h13M10 15h16M21 10l5 5-5 5" fill="none" stroke="#e8485a" stroke-width="1.6"/></svg>Log Out</div>
    </div>
  </header>

  <nav class="mainnav">
    <span style="left:27px">Home</span><span class="sep" style="left:118px">|</span>
    <span style="left:150px">eSource</span><span class="sep" style="left:264px">|</span>
    <span class="active" style="left:296px">eBuy</span><span class="sep" style="left:376px">|</span>
    <span style="left:408px">eRequest</span><span class="sep" style="left:535px">|</span>
    <span style="left:568px">eStock</span><span class="sep" style="left:666px">|</span>
    <span style="left:699px">ePlan</span><span class="sep" style="left:784px">|</span>
    <span style="left:815px">Preferences</span>
  </nav>
  <div class="abs brand">Brightmoor</div>

  <nav class="subnav">
    <span class="active" style="left:27px">Orders</span>
    <span style="left:118px">Receipts</span>
    <span style="left:227px">Shipments</span>
    <span style="left:355px">Invoices</span>
    <span style="left:459px">Pricing</span>
    <span style="left:555px">Tables</span>
    <span style="left:641px">Reports</span>
    <span style="left:742px">Inquiries</span>
    <span style="left:853px">Periodic Tasks</span>
    <span style="left:1014px">Workflows</span>
  </nav>
  <div class="abs subnav-bar"></div>
  <div class="abs rule"></div>

  <h1 class="abs title">Purchase Order</h1>

  <div class="abs lbl" style="left:35px;top:245px">Order #</div>
  <div class="abs val" style="left:111px;top:247px">100159</div>

  <div class="abs lbl" style="left:22px;top:282px">Ship from</div>
  <div class="abs field" style="left:101px;top:279px;width:105px">1001</div>
  <div class="abs link" style="left:215px;top:282px">/</div>
  <div class="abs field" style="left:230px;top:279px;width:33px">0</div>

  <div class="abs field focus" style="left:101px;top:315px;width:280px">Harbor Care Supplies|</div>
  <svg class="ico" style="left:393px;top:318px" width="22" height="22" viewBox="0 0 22 22"><g fill="none" stroke="#3d6fb8" stroke-width="1.3"><circle cx="11" cy="11" r="10"/><ellipse cx="11" cy="11" rx="4.5" ry="10"/><path d="M1 11h20M3 6h16M3 16h16M11 1v20"/></g></svg>

  <div class="abs lbl" style="left:33px;top:356px">Address</div>
  <div class="abs field" style="left:101px;top:351px;width:280px">14 Quarry Ln</div>
  <div class="abs field" style="left:101px;top:387px;width:280px"></div>
  <div class="abs link" style="left:399px;top:391px;font-size:14px">DPV Unconfirmed</div>

  <div class="abs lbl" style="left:60px;top:428px">City</div>
  <div class="abs field" style="left:101px;top:424px;width:203px">Westbrook</div>
  <div class="abs lbl" style="left:322px;top:428px">State</div>
  <div class="abs field" style="left:370px;top:424px;width:43px">MA</div>
  <svg class="ico" style="left:423px;top:428px" width="18" height="18" viewBox="0 0 18 18"><rect x="1" y="1" width="16" height="16" rx="3" fill="none" stroke="#5cbf3c" stroke-width="1.6"/><path d="M4.5 9l3 3 6-6" fill="none" stroke="#5cbf3c" stroke-width="1.8"/></svg>
  <div class="abs" style="left:446px;top:428px;font-size:14px;color:var(--green)">Accept</div>

  <div class="abs lbl" style="left:65px;top:465px">Zip</div>
  <div class="abs field" style="left:101px;top:461px;width:114px">01962-4410</div>
  <div class="abs lbl" style="left:230px;top:465px">Country</div>
  <div class="abs field" style="left:297px;top:461px;width:116px">US</div>
  <div class="abs link" style="left:437px;top:464px;text-decoration:underline">Add Contact</div>

  <aside class="abs sidebar">
    <div class="gray"></div>
    <div class="side-item" style="top:68px">Header</div>
    <div class="side-item done" style="top:220px"><svg width="26" height="26" viewBox="0 0 26 26"><circle cx="13" cy="13" r="13" fill="#5cbf3c"/><path d="M7 13l4 4 8-8" fill="none" stroke="#fff" stroke-width="2.4"/></svg>Lines</div>
    <div class="side-item" style="top:372px">Changes</div>
    <div class="side-item done" style="top:522px"><svg width="26" height="26" viewBox="0 0 26 26"><circle cx="13" cy="13" r="13" fill="#5cbf3c"/><path d="M7 13l4 4 8-8" fill="none" stroke="#fff" stroke-width="2.4"/></svg>Notes</div>
  </aside>

  <section class="abs panel"></section>
  <nav class="abs tabs"><span>Order Info</span><span class="active">Shipping</span><span>Payment</span><span>Accounts</span><span>Totals / Approval</span></nav>

  <div class="abs row-lbl" style="left:0;width:133px;top:576px">Receive At</div>
  <div class="abs select drop" style="left:142px;top:572px;width:151px"><i></i>ALCH</div>
  <div class="abs row-lbl" style="left:0;width:133px;top:609px">Carrier</div>
  <div class="abs select drop" style="left:142px;top:605px;width:151px"><i></i>Swiftline</div>
  <div class="abs row-lbl" style="left:0;width:133px;top:642px">Express Service</div>
  <div class="abs select drop" style="left:142px;top:638px;width:151px"><i></i></div>
  <div class="abs row-lbl" style="left:0;width:133px;top:676px">FOB</div>
  <div class="abs select drop" style="left:142px;top:672px;width:151px"><i></i></div>
  <div class="abs row-lbl" style="left:0;width:133px;top:710px">Order Ship Rule</div>
  <div class="abs select drop" style="left:142px;top:706px;width:192px"><i></i>Partials</div>
  <div class="abs row-lbl" style="left:0;width:133px;top:744px">Line Ship Rule</div>
  <div class="abs select drop" style="left:142px;top:740px;width:192px"><i></i>Partials</div>

  <div class="abs row-lbl" style="left:300px;width:133px;top:576px">Request Date</div>
  <div class="abs select" style="left:442px;top:572px;width:151px">01/07/2018</div>
  <svg class="ico" style="left:572px;top:575px" width="17" height="17" viewBox="0 0 17 17"><rect x="1" y="2" width="15" height="14" fill="none" stroke="#555" stroke-width="1.3"/><path d="M1 6h15M4 0v4M13 0v4" stroke="#555" stroke-width="1.3"/><g fill="#555"><rect x="3" y="8" width="2" height="2"/><rect x="7" y="8" width="2" height="2"/><rect x="11" y="8" width="2" height="2"/><rect x="3" y="12" width="2" height="2"/><rect x="7" y="12" width="2" height="2"/><rect x="11" y="12" width="2" height="2"/></g></svg>
  <div class="abs row-lbl" style="left:300px;width:133px;top:609px">Freight Terms</div>
  <div class="abs select drop" style="left:442px;top:605px;width:151px"><i></i>Collect</div>
  <div class="abs row-lbl" style="left:300px;width:133px;top:642px">Freight Calc</div>
  <div class="abs select drop" style="left:442px;top:638px;width:193px"><i></i></div>

  <div class="abs row-lbl" style="left:655px;top:574px">Customer Ship To</div>
  <div class="abs select" style="left:784px;top:569px;width:105px"></div>
  <div class="abs link" style="left:898px;top:572px">/</div>
  <div class="abs select" style="left:913px;top:569px;width:34px"></div>

  <svg class="ico" style="left:983px;top:734px" width="24" height="30" viewBox="0 0 24 30"><path d="M6 13V8a6 6 0 0112 0v5" fill="none" stroke="#3d6fb8" stroke-width="1.6"/><rect x="2" y="13" width="20" height="15" fill="none" stroke="#3d6fb8" stroke-width="1.6"/><path d="M2 23h20" stroke="#3d6fb8" stroke-width="1.2"/><text x="12" y="25" font-size="7" fill="#3d6fb8" text-anchor="middle" font-family="Open Sans, sans-serif">0</text></svg>

  <footer class="abs toolbar"></footer>
  <svg class="ico" style="left:17px;top:815px" width="28" height="28" viewBox="0 0 28 28"><path d="M20 8L9 19a3 3 0 004 4l12-12a5 5 0 00-7-7L6 16a7 7 0 0010 10" fill="none" stroke="#3d6fb8" stroke-width="2"/></svg>
  <svg class="ico" style="left:62px;top:813px" width="28" height="32" viewBox="0 0 28 32"><path d="M3 2h13l5 5v12M3 2v26h11" fill="none" stroke="#3d6fb8" stroke-width="1.5"/><path d="M7 10h10M7 14h10M7 18h6" stroke="#3d6fb8" stroke-width="1.3"/><circle cx="19" cy="23" r="4" fill="none" stroke="#3d6fb8" stroke-width="1.5"/><path d="M22 26l4 4" stroke="#3d6fb8" stroke-width="1.8"/></svg>
  <svg class="ico" style="left:103px;top:815px" width="28" height="28" viewBox="0 0 28 28"><g fill="#3d6fb8"><circle cx="6" cy="14" r="4.5"/><circle cx="22" cy="5" r="4.5"/><circle cx="22" cy="23" r="4.5"/></g><path d="M6 14L22 5M6 14l16 9" stroke="#3d6fb8" stroke-width="2.2"/></svg>
  <svg class="ico" style="left:155px;top:813px" width="32" height="32" viewBox="0 0 32 32"><rect x="2" y="8" width="28" height="21" fill="none" stroke="#3d6fb8" stroke-width="1.6"/><path d="M11 8V3h10v5M2 17h28" stroke="#3d6fb8" stroke-width="1.6" fill="none"/><rect x="13" y="15" width="6" height="5" fill="#fff" stroke="#3d6fb8" stroke-width="1.4"/></svg>
  <svg class="ico" style="left:210px;top:814px" width="31" height="31" viewBox="0 0 31 31"><circle cx="15.5" cy="15.5" r="14" fill="none" stroke="#7b7f87" stroke-width="2"/><path d="M11 12a4.5 4.5 0 119 0c0 3.5-4.5 3.5-4.5 7" fill="none" stroke="#7b7f87" stroke-width="2.2"/><circle cx="15.5" cy="23.5" r="1.6" fill="#7b7f87"/></svg>
  <svg class="ico" style="left:262px;top:815px" width="34" height="30" viewBox="0 0 34 30"><rect x="1" y="2" width="27" height="22" fill="none" stroke="#3d6fb8" stroke-width="2"/><rect x="1" y="2" width="27" height="5" fill="#3d6fb8"/><path d="M5 12h19M5 17h12" stroke="#3d6fb8" stroke-width="2"/><circle cx="28" cy="24" r="5.5" fill="#5cbf3c"/><path d="M28 21v6M25 24h6" stroke="#fff" stroke-width="1.6"/></svg>
  <div class="abs status">Enter property values, and click Apply</div>
  <svg class="ico" style="left:968px;top:813px" width="30" height="30" viewBox="0 0 30 30"><circle cx="12" cy="12" r="9.5" fill="none" stroke="#7b7f87" stroke-width="2.6"/><path d="M19 19l9 9" stroke="#7b7f87" stroke-width="3"/></svg>
  <svg class="ico" style="left:1011px;top:813px" width="30" height="30" viewBox="0 0 30 30"><path d="M15 1v28M1 15h28" stroke="#7b7f87" stroke-width="2.6"/></svg>
  <svg class="ico" style="left:1053px;top:811px" width="30" height="34" viewBox="0 0 30 34"><path d="M10 4L3 11l7 7" fill="none" stroke="#3d6fb8" stroke-width="3"/><path d="M3 11h13a9 9 0 010 18h-4" fill="none" stroke="#3d6fb8" stroke-width="3"/></svg>
  <svg class="ico" style="left:1096px;top:813px" width="36" height="30" viewBox="0 0 36 30"><path d="M2 15l10 11L34 3" fill="none" stroke="#5cbf3c" stroke-width="4"/></svg>
  <svg class="ico" style="left:1150px;top:814px" width="28" height="28" viewBox="0 0 28 28"><path d="M2 2l24 24M26 2L2 26" stroke="#e23a48" stroke-width="4"/></svg>

</div>
</body>
</html>
```